Business Card Design

We are a commercial real estate brokerage in San Francisco, leasing office buildings downtown.
I would like a clean, elegant look. Simple but powerful .

Industry/Entity Type

Business

Contact Information for Business Card

Derek Holloway
lic# 07258143
415.555.0172
derek@velt-commercial.example
velt-commercial.example

```html
<!DOCTYPE html>
<html lang="en">
<head>
<meta charset="utf-8">
<title>Velt Commercial — Business Card</title>
<link href="https://fonts.googleapis.com/css2?family=Source+Sans+3:wght@400;600&display=swap" rel="stylesheet">
<style>
  :root {
    --backdrop-top: #2a2a2a;
    --backdrop-bottom: #050505;
    --card: #ffffff;
    --brand-blue: #6a7d9c;
    --ink: #4a4a4a;
    --rule: #555555;
    --icon: #6a7d9c;
    --emboss: #e6e6e6;
  }
  * { box-sizing: border-box; margin: 0; padding: 0; }
  html, body {
    width: 1200px; height: 900px; overflow: hidden;
  }
  body {
    background: linear-gradient(180deg, var(--backdrop-top) 0%, #151515 55%, var(--backdrop-bottom) 100%);
    font-family: "Source Sans 3", "Myriad Pro", sans-serif;
    position: relative;
  }
  .card {
    position: absolute;
    background: var(--card);
    border-radius: 10px;
  }
  .card--front { left: 149px; top: 306px; width: 439px; height: 270px; }
  .card--back  { left: 608px; top: 306px; width: 441px; height: 272px; }

  .brand {
    position: absolute;
    display: flex;
    align-items: center;
    gap: 12px;
  }
  .brand__mark {
    width: 58px; height: 58px;
    background: var(--brand-blue);
  }
  .brand__name {
    font-weight: 600;
    color: var(--brand-blue);
    line-height: 0.95;
    text-transform: uppercase;
  }
  .brand__name span { display: block; }
  .card--front .brand { left: 18px; top: 106px; }
  .card--front .brand__name { font-size: 30px; }
  .card--front .brand__name .brand__sub { font-size: 17px; letter-spacing: 0.5px; }

  .card--back .brand { left: 72px; top: 92px; }
  .card--back .brand__mark { width: 86px; height: 86px; background: var(--emboss); }
  .card--back .brand__name { color: var(--emboss); font-size: 50px; }
  .card--back .brand__name .brand__sub { font-size: 27px; letter-spacing: 1px; }

  .contact {
    position: absolute;
    left: 219px; top: 80px;
    color: var(--ink);
  }
  .contact__name {
    font-size: 16px; font-weight: 600;
    color: var(--brand-blue);
    margin-bottom: 10px;
  }
  .contact__licence { font-size: 12.5px; margin-bottom: 17px; }
  .contact__list { list-style: none; }
  .contact__item {
    display: flex; align-items: center; gap: 9px;
    font-size: 12.5px; line-height: 16px;
  }
  .contact__item svg { width: 10px; height: 10px; flex: none; margin-left: 2px; }
</style>
</head>
<body>
  <section class="card card--front" aria-label="Card front">
    <div class="brand">
      <div class="brand__mark"></div>
      <div class="brand__name"><span>Velt</span><span class="brand__sub">Commercial</span></div>
    </div>
    <div class="contact">
      <p class="contact__name">Derek Holloway</p>
      <p class="contact__licence">Lic# 07258143</p>
      <ul class="contact__list">
        <li class="contact__item">
          <svg viewBox="0 0 10 10"><path fill="var(--icon)" d="M2 0.5l1.8 2-0.9 1.3c0.6 1.3 1.6 2.3 2.9 2.9l1.3-0.9 2 1.8-1 1.9C4.3 9.3 0.7 5.7 0.2 1.5z"/></svg>
          415.555.0172
        </li>
        <li class="contact__item">
          <svg viewBox="0 0 10 10"><rect x="0.5" y="2" width="9" height="6.5" fill="var(--icon)"/><path d="M0.8 2.3L5 5.6 9.2 2.3" stroke="#fff" stroke-width="0.9" fill="none"/></svg>
          derek@velt-commercial.example
        </li>
        <li class="contact__item">
          <svg viewBox="0 0 10 10"><circle cx="5" cy="5" r="4.3" fill="none" stroke="var(--icon)" stroke-width="1"/><ellipse cx="5" cy="5" rx="1.8" ry="4.3" fill="none" stroke="var(--icon)" stroke-width="0.8"/><path d="M0.8 5h8.4" stroke="var(--icon)" stroke-width="0.8"/></svg>
          velt-commercial.example
        </li>
      </ul>
    </div>
  </section>

  <section class="card card--back" aria-label="Card back">
    <div class="brand">
      <div class="brand__mark"></div>
      <div class="brand__name"><span>Velt</span><span class="brand__sub">Commercial</span></div>
    </div>
  </section>
</body>
</html>
```